Website redesign - vorelmik.com

We are looking to do a full redesign of vorelmik.com. Need a designer to come up overall layout and 3 specific pages and 3 different hero images.
Wireframes for the 3 pages are attached as well as site images. You don't have to follow the wireframes exactly, but instead the wireframe is there to show you the information that needs to be on each page. Feel free to rearrange as needed.
Our target market is self taught engineers. So definitely I want a more casual feel to it. I'm ok with fun bold colors as well. Really like websites that have the infinite scroll look/feel to them.
Looking to find a designer who will produce HTML and potentially even implement the HTML into our site checked in code.
HTML Code should be responsive/mobile first leveraging Bootstrap 4.
Attached files include:
0) Wireframe PDF
https://files.plomwerk.net/d/7Kx2pQmW9zLr4TbN8vYc3HsE5fJ/view?mode=share
1) Vorelmik Images zip 1
https://files.plomwerk.net/d/4Gt8nRvB2wQx6MkZ1pLd9YaC7hU/view?mode=share
2) Vorelmik Images zip 2
https://files.plomwerk.net/d/9Jw3sTcF5yNv1HqX8rKb2ZeM6dP/view?mode=share
Target Market(s)
I sell DIY Waterproof Electronics enclosures. Target audience is self taught DIY engineers
Coding
Coded - Design and coding required
Number of Pages Required
3 page
Colors
Designer to choose colors to be used in the design.
Look and feel

```html
<!DOCTYPE html>
<html lang="en">
<head>
<meta charset="utf-8">
<title>Vorelmik — Waterproof Project Boxes</title>
<link rel="stylesheet" href="https://fonts.googleapis.com/css2?family=Audiowide&family=Montserrat:wght@400;500;600&display=swap">
<style>
:root{
  --blue:#0d1fe6;
  --yellow:#e0b705;
  --yellow-dark:#c9a204;
  --ink:#111;
  --light:#f4f5f7;
  --card:#fff;
  --plate:#2b2c2e;
  --board:#3f7a4a;
  --steel:#b9bcc0;
}
*{box-sizing:border-box;margin:0;padding:0}
html,body{width:1200px;height:4481px;overflow:hidden;background:#fff}
body{font-family:"Montserrat",sans-serif;color:var(--ink);position:relative}
.tech{font-family:"Audiowide",sans-serif}
.abs{position:absolute}
.btn{position:absolute;display:flex;align-items:center;justify-content:center;font-family:"Audiowide",sans-serif;font-size:15px;color:#fff;text-decoration:none}
.btn--blue{background:var(--blue)}
.btn--yellow{background:var(--yellow)}
.photo{position:absolute}

/* header */
.site-header{position:absolute;top:0;left:0;width:1200px;height:80px;background:#fff}
.brand{left:98px;top:14px;font-size:40px;color:var(--blue);display:flex;align-items:center;gap:8px}
.brand-dot{width:12px;height:12px;border-radius:50%;background:var(--yellow)}
.nav{left:343px;top:40px;display:flex;gap:27px;font-size:15px;color:#222}
.btn--nav{top:22px;height:43px;width:137px;font-size:15px}

/* hero */
.hero{position:absolute;top:80px;left:0;width:1200px;height:616px;background:linear-gradient(90deg,#fff 0%,#f4f4f4 60%,#ececec 100%)}
.hero h1{position:absolute;left:100px;top:180px;font-size:45px;font-weight:600;line-height:61px;width:520px}
.hero-product{left:660px;top:110px;width:530px;height:440px;border-radius:14px;
  background:linear-gradient(160deg,#e6e7e9 0%,var(--steel) 22%,var(--board) 42%,#2f5e3a 58%,var(--plate) 78%,#4a4b4e 100%);
  box-shadow:0 24px 40px -20px rgba(0,0,0,.35)}

/* designer */
.section-title{font-family:"Audiowide",sans-serif;color:var(--ink);font-weight:400}
.play{position:absolute;left:296px;top:912px;width:82px;height:82px;border-radius:50%;background:var(--yellow);display:flex;align-items:center;justify-content:center}

/* band */
.band{position:absolute;top:1212px;left:0;width:1200px;height:394px;background:linear-gradient(135deg,var(--yellow) 0%,#d9b007 50%,var(--yellow-dark) 100%)}
.arrow-btn{position:absolute;top:1762px;width:45px;height:44px;border:1px solid #ccc;display:flex;align-items:center;justify-content:center;background:#fff}
.kit-dark{background:linear-gradient(180deg,#4a4b4e,#2f3032 60%,#3a3b3d)}
.kit-light{background:linear-gradient(180deg,#e9eaec 0%,#c6c9cd 45%,#7d8a80 62%,#d6d8db 100%)}
.kit-main{background:linear-gradient(180deg,#eef0f6 0%,#d5d9e4 30%,#4f8a5a 52%,#2a2b2d 70%,#dfe2ea 100%)}

/* makers list */
.features{position:absolute;left:100px;top:2110px;list-style:none;font-size:18px;line-height:28px;color:#222;width:440px}
.features li{display:flex;gap:16px;margin-bottom:15px}
.features svg{flex:none;margin-top:4px}

/* testimonials */
.reviews{position:absolute;top:2533px;left:0;width:1200px;height:565px;background:var(--light)}
.review{position:absolute;top:2758px;width:475px;height:242px;background:var(--card);text-align:center;box-shadow:0 8px 0 -2px #e6e7ea}
.review .quote{position:absolute;left:194px;top:-36px;width:87px;height:87px;border-radius:50%;background:var(--yellow);display:flex;align-items:center;justify-content:center}
.review h3{margin-top:68px;font-weight:500;font-size:20px}
.review p{margin:14px auto 0;width:410px;font-size:15px;line-height:28px;color:#333}
.side-arrow{position:absolute;top:2862px;width:16px;height:24px;display:flex;align-items:center;justify-content:center}

/* examples */
.example{position:absolute;width:318px;text-align:center}
.example .thumb{width:318px;height:221px;border:1px solid #eee}
.thumb--kit{background:linear-gradient(180deg,#f6f6f7 0%,#d2d4d7 30%,#4e7f57 48%,#2a2b2d 66%,#f3f3f4 90%)}
.thumb--psu{background:linear-gradient(180deg,#f6f6f7 0%,#c9ccd0 32%,#9ea2a6 48%,#2a2b2d 68%,#f3f3f4 90%)}
.thumb--clear{background:linear-gradient(180deg,#f6f6f7 0%,#efe6ee 30%,#e2d3e0 55%,#f3f3f4 88%)}
.thumb--green{background:linear-gradient(180deg,#f6f6f7 0%,#3c4a3c 35%,#1f2a22 62%,#f3f3f4 90%)}
.thumb--olive{background:linear-gradient(180deg,#f6f6f7 0%,#6c7256 32%,#4f553e 62%,#f3f3f4 90%)}
.example h4{margin-top:22px;font-size:21px;font-weight:500}
.example span{display:block;margin-top:6px;font-size:14px;color:#333}

/* footer */
.site-footer{position:absolute;top:4410px;left:0;width:1200px;height:71px;background:var(--blue);color:#fff;font-size:15px}
.social{width:36px;height:36px;border-radius:50%;position:absolute;top:17px}
</style>
</head>
<body>

<header class="site-header">
  <div class="abs brand tech"><span class="brand-dot"></span>Vorelmik</div>
  <nav class="abs nav"><span>Get Started</span><span>Designs</span><span>FAQ's</span><span>Videos</span><span>Contact Us</span></nav>
  <a class="btn btn--yellow btn--nav" style="left:818px">Sign In</a>
  <a class="btn btn--blue btn--nav" style="left:964px">Sign Up</a>
</header>

<section class="hero">
  <h1>Waterproof Project Boxes Customized To Your Exact Needs.</h1>
  <a class="btn btn--yellow" style="left:98px;top:388px;width:164px;height:44px">Get Started</a>
  <div class="photo hero-product" role="img" aria-label="Assembled project box mounting plate with circuit boards and standoffs"></div>
</section>

<div class="photo" role="img" aria-label="Video thumbnail of laser-cut black mounting plates" style="left:97px;top:782px;width:482px;height:344px;border-radius:6px;background:linear-gradient(180deg,#9a9ba0 0%,#7c7d82 25%,#26272a 40%,#1d1e20 70%,#8d8e93 100%)"></div>
<div class="play"><svg width="26" height="30" viewBox="0 0 26 30"><path d="M4 1 L25 15 L4 29Z" fill="#fff"/></svg></div>
<h2 class="abs section-title" style="left:648px;top:868px;font-size:29px;line-height:48px;width:450px">Customize your Project Box using our Designer</h2>
<a class="btn btn--blue" style="left:647px;top:981px;width:163px;height:43px">Get Started</a>

<section class="band">
  <h2 class="abs section-title" style="left:0;width:1200px;top:80px;text-align:center;font-size:29px;line-height:48px">Mounting Kits for all the popular water proof<br>project boxes with many sizes to choose from</h2>
  <a class="btn btn--blue" style="left:518px;top:201px;width:163px;height:44px">Get Started</a>
</section>
<div class="photo kit-dark" role="img" aria-label="Mounting kit example" style="left:115px;top:1540px;width:130px;height:166px"></div>
<div class="photo kit-dark" role="img" aria-label="Mounting kit example" style="left:955px;top:1540px;width:130px;height:166px"></div>
<div class="photo kit-light" role="img" aria-label="Mounting kit example" style="left:243px;top:1523px;width:155px;height:200px"></div>
<div class="photo kit-light" role="img" aria-label="Mounting kit example" style="left:805px;top:1523px;width:178px;height:200px"></div>
<div class="photo kit-main" role="img" aria-label="Featured mounting kit with stacked circuit boards" style="left:396px;top:1507px;width:409px;height:235px;border:1px solid #c9cde8"></div>
<div class="arrow-btn" style="left:547px"><svg width="22" height="10" viewBox="0 0 22 10"><path d="M21 5H2M6 1L2 5l4 4" stroke="#555" stroke-width="1.6" fill="none"/></svg></div>
<div class="arrow-btn" style="left:607px"><svg width="22" height="10" viewBox="0 0 22 10"><path d="M1 5h19M16 1l4 4-4 4" stroke="var(--yellow)" stroke-width="1.8" fill="none"/></svg></div>

<h2 class="abs section-title" style="left:100px;top:1965px;font-size:23px;line-height:38px;width:420px">Vorelmik waterproof project boxes were built by makers for makers</h2>
<ul class="features">
  <li><svg width="18" height="18" viewBox="0 0 18 18"><rect x="1" y="3" width="13" height="13" fill="none" stroke="var(--blue)" stroke-width="1.6"/><path d="M4 9l3 3 9-10" stroke="var(--blue)" stroke-width="1.8" fill="none"/></svg>Design to your specifications</li>
  <li><svg width="18" height="18" viewBox="0 0 18 18"><rect x="1" y="3" width="13" height="13" fill="none" stroke="var(--blue)" stroke-width="1.6"/><path d="M4 9l3 3 9-10" stroke="var(--blue)" stroke-width="1.8" fill="none"/></svg>Maker components: Nanoboard, Quartzberry, Steadywatt Power</li>
  <li><svg width="18" height="18" viewBox="0 0 18 18"><rect x="1" y="3" width="13" height="13" fill="none" stroke="var(--blue)" stroke-width="1.6"/><path d="M4 9l3 3 9-10" stroke="var(--blue)" stroke-width="1.8" fill="none"/></svg>Detailed build instructions, videos, walkthroughs</li>
  <li><svg width="18" height="18" viewBox="0 0 18 18"><rect x="1" y="3" width="13" height="13" fill="none" stroke="var(--blue)" stroke-width="1.6"/><path d="M4 9l3 3 9-10" stroke="var(--blue)" stroke-width="1.8" fill="none"/></svg>DIY made to look professional</li>
</ul>
<a class="btn btn--blue" style="left:98px;top:2362px;width:164px;height:44px">Get Started</a>
<div class="photo" style="left:910px;top:1895px;width:230px;height:225px;background-image:radial-gradient(#dcdde2 2px,transparent 2.5px);background-size:12px 12px"></div>
<div class="photo" role="img" aria-label="Close-up of power supply and circuit boards mounted on a black plate" style="left:618px;top:1933px;width:482px;height:515px;background:linear-gradient(155deg,#c4c6ca 0%,#9a9da1 25%,#4d7d55 45%,#2f5a39 58%,#232426 78%,#333436 100%)"></div>

<section class="reviews">
  <h2 class="abs section-title" style="left:0;width:1200px;top:85px;text-align:center;font-size:29px">What Our Customers Have To Say</h2>
</section>
<div class="side-arrow" style="left:90px"><svg width="10" height="16" viewBox="0 0 10 16"><path d="M8 2L2 8l6 6" stroke="#333" stroke-width="2" fill="none"/></svg></div>
<div class="side-arrow" style="left:1092px"><svg width="10" height="16" viewBox="0 0 10 16"><path d="M2 2l6 6-6 6" stroke="#333" stroke-width="2" fill="none"/></svg></div>
<article class="review" style="left:98px">
  <div class="quote"><svg width="44" height="36" viewBox="0 0 44 36"><path d="M4 34V18C4 9 9 3 18 2v6c-5 1-7 4-7 9h7v17zM26 34V18c0-9 5-15 14-16v6c-5 1-7 4-7 9h7v17z" fill="none" stroke="#fff" stroke-width="2.5"/></svg></div>
  <h3>Marten D</h3>
  <p>Great work at a reasonable cost. I can't recommend them enough. If you're doing custom boxes for light shows, this is where you go.</p>
</article>
<article class="review" style="left:627px">
  <div class="quote"><svg width="44" height="36" viewBox="0 0 44 36"><path d="M4 34V18C4 9 9 3 18 2v6c-5 1-7 4-7 9h7v17zM26 34V18c0-9 5-15 14-16v6c-5 1-7 4-7 9h7v17z" fill="none" stroke="#fff" stroke-width="2.5"/></svg></div>
  <h3>Oskar H</h3>
  <p>Fantastic service/product.. whether you simply generate the design and do all of the fabrication yourself or simply order the kits.</p>
</article>

<h2 class="abs section-title" style="left:0;width:1200px;top:3184px;text-align:center;font-size:29px">See Real Examples From Our Customers</h2>
<div class="example" style="left:98px;top:3265px"><div class="thumb thumb--kit" role="img" aria-label="CrateBox 32026 mounting kit"></div><h4>CrateBox 32026</h4><span>Standalone Primary</span></div>
<div class="example" style="left:441px;top:3265px"><div class="thumb thumb--kit" role="img" aria-label="CrateBox 32022 mounting kit"></div><h4>CrateBox 32022</h4><span>Standalone Primary</span></div>
<div class="example" style="left:784px;top:3265px"><div class="thumb thumb--kit" role="img" aria-label="CrateBox 32016 mounting kit"></div><h4>CrateBox 32016</h4><span>Standalone Primary</span></div>
<div class="example" style="left:98px;top:3608px"><div class="thumb thumb--psu" role="img" aria-label="CrateBox 32012 mounting kit with power supply"></div><h4>CrateBox 32012</h4><span>Standalone Primary</span></div>
<div class="example" style="left:441px;top:3608px"><div class="thumb thumb--psu" role="img" aria-label="CrateBox 32010 mounting kit with power supply"></div><h4>CrateBox 32010</h4><span>Standalone Top</span></div>
<div class="example" style="left:784px;top:3608px"><div class="thumb thumb--psu" role="img" aria-label="kv1500 mounting kit"></div><h4>kv1500</h4><span>Standalone Primary</span></div>
<div class="example" style="left:98px;top:3954px"><div class="thumb thumb--clear" role="img" aria-label="kv500 clear project box"></div><h4>kv500</h4><span>Project Box</span></div>
<div class="example" style="left:441px;top:3954px"><div class="thumb thumb--green" role="img" aria-label="rtn30 dark green project box"></div><h4>rtn30</h4><span>Project Box</span></div>
<div class="example" style="left:784px;top:3954px"><div class="thumb thumb--olive" role="img" aria-label="stc4 olive project box"></div><h4>stc4</h4><span>Project Box</span></div>
<a class="btn btn--blue" style="left:518px;top:4296px;width:163px;height:44px">View All</a>

<footer class="site-footer">
  <span class="abs" style="left:98px;top:26px">Copyright © 2019 Vorelmik designer. All Rights Reserved.</span>
  <span class="abs" style="left:903px;top:27px">Follow Us On:</span>
  <span class="social" style="left:1022px;border:2px solid #fff"></span>
  <span class="social" style="left:1066px;background:#e02a2a;border:2px solid #fff"></span>
</footer>

</body>
</html>
```